Local Roofing/Construction company business needs new biz card design

We need a new business card design, current cards are from the start of this operation and generic at best. We are a local Construction Company (General Contractor) with a majority of our work originating from insurance claims-exterior finish work is the main focus (Roofs-Siding-Gutters etc). Heavily involved with homeowners and the low ball offers they receive from insurance company's after a insurable event takes place. I have attached some of our original logo file(s) below.

```html
<!DOCTYPE html>
<html lang="en">
<head>
<meta charset="utf-8">
<title>Northgate Builders – Business Card</title>
<link href="https://fonts.googleapis.com/css2?family=Exo+2:wght@400;600;800&display=swap" rel="stylesheet">
<style>
  :root {
    --backdrop: #2a2a2a;
    --card-green: #33d97c;
    --card-green-deep: #22b463;
    --ink-dark: #0f1f22;
    --ink-light: #ffffff;
  }
  * { margin: 0; padding: 0; box-sizing: border-box; }
  html, body {
    width: 1200px; height: 689px; overflow: hidden;
    background: var(--backdrop);
    font-family: "Exo 2", sans-serif;
  }
  .canvas {
    position: relative; width: 1200px; height: 689px;
    display: flex; align-items: center; justify-content: center; gap: 40px;
  }
  .card {
    width: 540px; height: 320px; border-radius: 24px;
    background: var(--card-green);
    position: relative; overflow: hidden;
  }
  .card-back {
    display: flex; align-items: center; justify-content: center;
  }
  .card-back .brand-mark {
    font-weight: 800; font-size: 46px; letter-spacing: 2px;
    color: var(--card-green-deep); text-transform: uppercase;
    text-align: center; line-height: 1.05;
  }
  .card-front {
    display: flex; flex-direction: column; align-items: center;
    padding: 54px 36px 0;
  }
  .brand-name {
    font-weight: 800; font-size: 34px; letter-spacing: 1.5px;
    color: var(--ink-dark); text-transform: uppercase; line-height: 1;
    display: flex; align-items: center; gap: 12px; white-space: nowrap;
  }
  .brand-name .brand-square {
    width: 26px; height: 26px; background: var(--ink-dark); border-radius: 4px;
  }
  .person { margin-top: 44px; text-align: center; color: var(--ink-light); }
  .person-name { font-weight: 800; font-size: 24px; letter-spacing: 1px; text-transform: uppercase; }
  .person-role { font-weight: 400; font-size: 16px; margin-top: 2px; }
  .divider {
    width: 440px; height: 1px; background: var(--ink-light); opacity: .85;
    margin-top: 40px;
  }
  .contact {
    margin-top: 14px; display: flex; gap: 18px; align-items: center;
    color: var(--ink-light); font-size: 14px; white-space: nowrap;
  }
  .contact-item { display: flex; align-items: center; gap: 6px; }
  .contact-item svg { width: 14px; height: 14px; flex: none; fill: none; stroke: var(--ink-light); stroke-width: 1.6; }
</style>
</head>
<body>
<main class="canvas">
  <section class="card card-back">
    <div class="brand-mark">Northgate<br>Builders</div>
  </section>

  <section class="card card-front">
    <div class="brand-name"><span class="brand-square"></span>Northgate Builders</div>
    <div class="person">
      <div class="person-name">Daniel Reyes</div>
      <div class="person-role">Managing Director</div>
    </div>
    <div class="divider"></div>
    <div class="contact">
      <span class="contact-item">
        <svg viewBox="0 0 16 16"><path d="M3 2h3l1.5 3.5-2 1.2a8 8 0 0 0 3.8 3.8l1.2-2L14 10v3a1 1 0 0 1-1 1A11 11 0 0 1 2 3a1 1 0 0 1 1-1z"/></svg>
        055-318 402 716
      </span>
      <span class="contact-item">
        <svg viewBox="0 0 16 16"><rect x="1.5" y="3.5" width="13" height="9"/><path d="M1.5 3.5 8 9l6.5-5.5"/></svg>
        hello@northgate.co
      </span>
      <span class="contact-item">
        <svg viewBox="0 0 16 16"><circle cx="8" cy="8" r="6.5"/><path d="M1.5 8h13M8 1.5c-3 3.5-3 9.5 0 13M8 1.5c3 3.5 3 9.5 0 13"/></svg>
        www.northgate.co
      </span>
    </div>
  </section>
</main>
</body>
</html>
```